Postcard Design

Hi thereI would like a simple postcard for my online kids clothing and decor business. The brand colours are black, white and gold. I want enough white space so I can write personal messages. The logo to be placed at the top and with gold stars scattered around the outside. At the bottom of the card in the middle I want website, facebook page and instragram page. Take a look at the example postcard attached to get a good feel of my requirements. website is www.jaxonrose.comFacebook is facebook.com/Jaxon RoseInstagram is @jaxonrose_storeEmail is hello@milbrenvale.com
Industry/Entity Type
Business
Look and feel
Each slider illustrates characteristics of the customer's brand and the style your logo design should communicate.

```html
<!DOCTYPE html>
<html lang="en">
<head>
<meta charset="utf-8">
<title>Milbren Vale – Postcard</title>
<link href="https://fonts.googleapis.com/css2?family=Bebas+Neue&family=Lato:ital,wght@0,400;0,700;0,900;1,400;1,700&family=Roboto+Condensed:wght@400;500&display=swap" rel="stylesheet">
<style>
  :root {
    --gold: #c9992b;
    --gold-deep: #b8861f;
    --charcoal: #3b3b3c;
    --ink: #3a3a3a;
    --white: #ffffff;
    --paper-grey: #e4e4e4;
    --stage: #ecebea;
    --stamp: #d2d2d2;
    --photo-sky: #a9c4d6;
    --photo-warm: #c9a48d;
    --photo-store: #c7b7b4;
  }
  * { box-sizing: border-box; margin: 0; padding: 0; }
  html, body { width: 900px; height: 1200px; overflow: hidden; }
  body { background: var(--stage); font-family: "Lato", sans-serif; position: relative; }

  .card { position: absolute; left: 115px; width: 658px; overflow: hidden; background: var(--white); }
  .card--front { top: 65px; height: 508px; background: linear-gradient(180deg, #ffffff 0%, #f1f1f1 55%, #dcdcdc 100%); }
  .card--back { top: 640px; height: 512px; }

  .front-shapes { position: absolute; inset: 0; }

  .front-title { position: absolute; left: 25px; top: 26px; font: 900 38px/1 "Lato", sans-serif; color: var(--ink); letter-spacing: 0.3px; }
  .front-subtitle { position: absolute; left: 26px; top: 70px; font: italic 400 20px/1.1 "Lato", sans-serif; color: var(--gold-deep); }
  .front-body { position: absolute; left: 26px; top: 105px; width: 272px; font: italic 400 12.6px/16.6px "Lato", sans-serif; color: var(--ink); text-align: justify; }

  .contact-band { position: absolute; left: 0; top: 234px; width: 278px; height: 36px; background: var(--gold); border-radius: 0 18px 18px 0; box-shadow: 0 2px 3px rgba(0,0,0,.25); }
  .contact-band__text { position: absolute; left: 26px; top: 7px; font: italic 400 19px/1.1 "Lato", sans-serif; color: var(--white); }

  .feature-photo { position: absolute; left: 320px; top: 24px; width: 312px; height: 312px; border-radius: 50%; border: 8px solid var(--gold); box-shadow: 0 0 0 5px var(--white); background: linear-gradient(180deg, var(--photo-sky) 0%, #d7dde0 45%, var(--photo-warm) 100%); }

  .tagline { position: absolute; left: 26px; top: 292px; font: 700 21px/1.1 "Lato", sans-serif; color: var(--gold); }
  .tagline-sub { position: absolute; left: 26px; top: 323px; font: italic 400 20px/1.1 "Lato", sans-serif; color: var(--white); }

  .mini-photo { position: absolute; top: 367px; width: 126px; height: 126px; border-radius: 50%; border: 5px solid var(--gold); box-shadow: 0 0 0 4px var(--white); }
  .mini-photo--one { left: 23px; background: linear-gradient(180deg, #f4f1ee 0%, #e6cfd3 100%); }
  .mini-photo--two { left: 161px; background: linear-gradient(180deg, #cfe0ea 0%, #8b6d58 100%); }

  .brand { position: absolute; left: 322px; top: 392px; width: 134px; text-align: center; font: 700 22px/1.05 "Lato", sans-serif; color: var(--white); }
  .divider { position: absolute; left: 467px; top: 368px; width: 1px; height: 84px; background: #8a8a8a; }
  .visit { position: absolute; left: 484px; top: 372px; font: 400 34px/1 "Lato", sans-serif; color: var(--white); letter-spacing: 0.5px; }
  .visit__today { display: block; margin-top: 4px; color: var(--gold); }

  .front-footer { position: absolute; left: 0; bottom: 0; width: 100%; height: 28px; background: var(--gold); }
  .front-footer__text { position: absolute; right: 14px; top: 7px; font: 400 11px/1.2 "Roboto Condensed", sans-serif; color: var(--white); }

  .back-panel { position: absolute; left: 0; top: 0; width: 310px; height: 470px; background: var(--charcoal); }
  .back-rule { position: absolute; left: 310px; top: 0; width: 7px; height: 470px; background: var(--paper-grey); }
  .back-photo { position: absolute; left: -20px; top: -8px; width: 330px; height: 262px; border: 6px solid var(--gold); border-top: 0; border-radius: 0 0 190px 150px / 0 0 80px 60px; background: linear-gradient(120deg, var(--photo-store) 0%, #ece6df 50%, #d99a86 100%); }
  .back-body { position: absolute; left: 30px; top: 288px; width: 260px; font: italic 400 12.6px/16.6px "Lato", sans-serif; color: #e6e6e6; text-align: justify; }
  .back-contact { position: absolute; left: 27px; top: 408px; font: 400 31px/1 "Bebas Neue", sans-serif; color: var(--gold); letter-spacing: 0.3px; }

  .stamp-box { position: absolute; left: 554px; top: 29px; width: 74px; height: 75px; background: var(--stamp); }

  .back-footer { position: absolute; left: 0; bottom: 0; width: 100%; height: 42px; background: var(--gold); border-top: 4px solid var(--paper-grey); }
  .back-footer__text { position: absolute; left: 0; right: 0; top: 8px; text-align: center; font: 500 17px/1.2 "Roboto Condensed", sans-serif; color: var(--white); }
</style>
</head>
<body>

<section class="card card--front" aria-label="Postcard front">
  <svg class="front-shapes" width="658" height="508" viewBox="0 0 658 508" aria-hidden="true">
    <path d="M270 236 C420 228 560 210 658 196 L658 318 C540 300 420 276 270 272 Z" fill="var(--gold)"/>
    <path d="M0 270 L270 270 C420 282 540 310 658 330 L658 508 L0 508 Z" fill="var(--charcoal)"/>
  </svg>

  <h1 class="front-title">OPENING SOON</h1>
  <p class="front-subtitle">Milbren Vale’s Personal messages</p>
  <p class="front-body">Lorem ipsum dolor sit amet, consectetuer adipiscing elit, sed diam nonummy nibh euismod tincidunt ut laoreet dolore magna aliquam erat volutpat.Lorem ipsum dolor sit amet, consectetuer adipiscing elit, sed diam nonummy nibh euismod tincivolutpat.</p>

  <div class="contact-band"><p class="contact-band__text">Contact us at - 123.456.78</p></div>

  <div class="feature-photo" role="img" aria-label="Photo of a group of smiling young friends outdoors giving a thumbs up"></div>

  <p class="tagline">Lorel ipsum dolor sit amet</p>
  <p class="tagline-sub">Ut wisi enim ad minim veniam</p>

  <div class="mini-photo mini-photo--one" role="img" aria-label="Photo of a little girl in sunglasses holding a shopping bag"></div>
  <div class="mini-photo mini-photo--two" role="img" aria-label="Photo of a young child in sunglasses and a leather jacket"></div>

  <p class="brand">Milbren Vale</p>
  <span class="divider" aria-hidden="true"></span>
  <p class="visit">VISIT US<span class="visit__today">TODAY!</span></p>

  <footer class="front-footer">
    <p class="front-footer__text">facebook.com/Milbren Vale | Instagram - @milbrenvale_store | Email - hello@milbrenvale.com</p>
  </footer>
</section>

<section class="card card--back" aria-label="Postcard back">
  <div class="back-panel">
    <div class="back-photo" role="img" aria-label="Photo of a mother fitting a white party dress on her daughter in a clothing store"></div>
    <p class="back-body">Lorem ipsum dolor sit amet, consectetuer adipiscing elit, sed diam nonummy nibh euismod tincidunt ut laoreet dolore magna aliquam erat volutpat.Lorem ipsum dolor sit amet, consectetuer adipiscing elit, sed diam nonummy nibh euismod tincivolutpat.</p>
    <p class="back-contact">CONTACT US AT - 123.456.78</p>
  </div>
  <span class="back-rule" aria-hidden="true"></span>

  <div class="stamp-box" aria-label="Stamp area"></div>

  <footer class="back-footer">
    <p class="back-footer__text">facebook.com/Milbren Vale | Instagram - @milbrenvale_store | Email - hello@milbrenvale.com</p>
  </footer>
</section>

</body>
</html>
```